2 x Digitize Logo | 2 x Business Cards | 2 x Fridge Magnets

We require 6 deliverables:
1. Residential logo redrawn (same just high quality for large print format).
2. Corporate logo redrawn (minor changes to wording and high quality for large print format).
3. New business card design for Furniture Removals (residential)
4. New business card design for Corporate Relocations (business)
5. New Fridge magnet for Furniture removals (residential)
6. New fridge magnet for Corporate Relocations (business)
1. Residential Logo
a. We require the logo to be translated into a high quality digital image with no modifications.
(see attached resilogo.jpg)
2. Residential Logo
a. We require the logo to be edited (add the word corporate relocations) be translated into a high quality digital image.
(see attached corplogo.jpg)
3. Using the resilogo please make a new business card for our business.
a. Please see the web site https://www.larkbendcarters.com.au for colours and inspiration.
b. The residential business card needs the following information:
i. Business Name (using the residential logo).
ii. Free Call: 1800 LB Cart (the L, B and Cart much be the same colour as the logo).
iii. Website: www.LarkbendCarters.com.au
iv. Address: 4/17 Ormsdale Court, VIC 3264
v. Email: cart@LarkbendCarters.com.au
vi. backof Card:
Review our service
www.PennantOrbit.com.au
Services: Local, Country, Interstate | Furniture Removals | Piano, Billiard Tables & Antiques
4. Using the corplogo please make a new business card for our business.
b. The corporate business card needs the following information:
i. Business Name (using the corporate logo).
v. Email: corporate@LarkbendCarters.com.au
vi. Back of Card:
Review our service
www.PennantOrbit.com.au
Services: Corporate relocations | Office equipment moves | Packing Service | Packing Materials
5. Using the resilogo please make a new fridge magent for our business.
b. The residential fidge magnet needs the following information:
iv. Services: Local, Country, Interstate | Furniture Removals | Piano, Billiard Tables & Antiques
6. Using the corplogo please make a new fridge magent for our business.
b. The corporate fidge magnet needs the following information:
iv. Services: Local, Country, Interstate | Corporate relocations
Target Market(s)
Residential Furniture Removals and Corporate Office relocations
Industry/Entity Type
Business
Contact Information for Business Card
Please see full brief for six items required
Requirements
Must have
- Clean simple, easy to read
Nice to have
- fresh, stand out, eye catching
Should not have
- plain, standard, boring, general

```html
<!DOCTYPE html>
<html lang="en">
<head>
<meta charset="utf-8">
<title>Larkbend Carters – Business Cards</title>
<link rel="stylesheet" href="https://fonts.googleapis.com/css2?family=Cabin:wght@400;500;700&display=swap">
<style>
  :root {
    --green: #22b24c;
    --yellow: #f7c600;
    --red: #e31e24;
    --ink: #222222;
    --paper: #ffffff;
    --backdrop: #eceeef;
  }
  * { margin: 0; padding: 0; box-sizing: border-box; }
  html, body { width: 1109px; height: 1200px; overflow: hidden; }
  body {
    background: var(--backdrop);
    font-family: "Cabin", sans-serif;
    color: var(--ink);
    position: relative;
  }
  .card {
    position: absolute;
    left: 124px;
    width: 860px;
    height: 532px;
    background: var(--paper);
    box-shadow: 0 6px 18px rgba(0,0,0,0.18);
    overflow: hidden;
  }
  .card--front { top: 48px; }
  .card--back { top: 620px; }
  .card__shape { position: absolute; inset: 0; width: 100%; height: 100%; }

  .wordmark {
    position: absolute;
    width: 500px;
    text-align: center;
    font-weight: 700;
    font-size: 46px;
    letter-spacing: 1px;
    text-transform: uppercase;
    color: var(--green);
    line-height: 60px;
  }
  .card--front .wordmark { left: 316px; top: 62px; }
  .card--back .wordmark { left: 41px; top: 86px; }

  .services { position: absolute; left: 46px; top: 332px; color: var(--paper); }
  .services__title { font-size: 26px; font-weight: 400; line-height: 32px; margin-bottom: 10px; }
  .services__list { list-style: none; font-size: 23px; line-height: 31px; }
  .services__list li::before {
    content: ""; display: inline-block; width: 10px; height: 10px;
    border-radius: 50%; background: var(--paper); margin-right: 8px; vertical-align: 3px;
  }

  .contact { position: absolute; list-style: none; font-size: 23px; line-height: 31px; }
  .contact li { display: flex; align-items: center; gap: 8px; white-space: nowrap; }
  .contact li.contact__address { margin-top: 10px; }
  .card--front .contact { right: 30px; top: 351px; }
  .card--front .contact li { justify-content: flex-end; }
  .card--back .contact { left: 45px; top: 351px; }
  .icon { width: 18px; height: 18px; flex: none; fill: var(--green); }
  .phone-l { color: var(--yellow); font-weight: 700; }
  .phone-b { color: var(--red); font-weight: 700; }
  .phone-cart { color: var(--green); font-weight: 500; }

  .review { position: absolute; left: 515px; width: 260px; top: 420px; text-align: center; }
  .review__title { color: var(--yellow); font-weight: 700; font-size: 22px; line-height: 32px; text-transform: uppercase; }
  .review__link { color: var(--paper); font-size: 22px; line-height: 34px; }
</style>
</head>
<body>

<svg width="0" height="0" style="position:absolute" aria-hidden="true">
  <defs>
    <symbol id="i-phone" viewBox="0 0 24 24"><path d="M6.6 10.8a15.1 15.1 0 0 0 6.6 6.6l2.2-2.2a1 1 0 0 1 1-.25 11.4 11.4 0 0 0 3.6.57 1 1 0 0 1 1 1V20a1 1 0 0 1-1 1A17 17 0 0 1 3 4a1 1 0 0 1 1-1h3.5a1 1 0 0 1 1 1c0 1.25.2 2.450.57 3.57a1 1 0 0 1-.25 1z"/></symbol>
    <symbol id="i-mail" viewBox="0 0 24 24"><path d="M2 5h20v14H2z M4 7v.5l8 5 8-5V7l-8 5z" fill-rule="evenodd"/></symbol>
    <symbol id="i-globe" viewBox="0 0 24 24"><path d="M12 2a10 10 0 1 0 0 20 10 10 0 0 0 0-20zm-1 17.9A8 8 0 0 1 4.2 10.2L9 15v1a2 2 0 0 0 2 2zm6.9-2.5A2 2 0 0 0 16 16h-1v-3a1 1 0 0 0-1-1H8v-2h2a1 1 0 0 0 1-1V7h2a2 2 0 0 0 2-2v-.4a8 8 0 0 1 2.9 12.8z"/></symbol>
    <symbol id="i-pin" viewBox="0 0 24 24"><path d="M12 2a7 7 0 0 0-7 7c0 5.2 7 13 7 13s7-7.8 7-13a7 7 0 0 0-7-7zm0 9.5A2.5 2.5 0 1 1 12 6.5a2.5 2.5 0 0 1 0 5z"/></symbol>
  </defs>
</svg>

<section class="card card--front" aria-label="Business card front">
  <svg class="card__shape" viewBox="0 0 653 404" preserveAspectRatio="none" aria-hidden="true">
    <polygon points="0,0 275,0 205,62 345,404 0,404" fill="var(--green)"/>
    <polyline points="278,0 206,61 348,404" fill="none" stroke="var(--yellow)" stroke-width="4"/>
  </svg>
  <div class="wordmark">Larkbend Carters</div>

  <div class="services">
    <h2 class="services__title">SERVICES</h2>
    <ul class="services__list">
      <li>Local, Country, Interstate</li>
      <li>Furniture Removals</li>
      <li>Piano, Billiard Tables &amp; Antiques</li>
    </ul>
  </div>

  <ul class="contact">
    <li><span>1800 <span class="phone-l">L</span><span class="phone-b">B</span> <span class="phone-cart">Cart</span> / 1800 52 27 84</span><svg class="icon"><use href="#i-phone"/></svg></li>
    <li><span>cart@LarkbendCarters.com.au</span><svg class="icon"><use href="#i-mail"/></svg></li>
    <li><span>www.LarkbendCarters.com.au</span><svg class="icon"><use href="#i-globe"/></svg></li>
    <li class="contact__address"><span>4/17 Ormsdale Court, VIC 3264</span><svg class="icon"><use href="#i-pin"/></svg></li>
  </ul>
</section>

<section class="card card--back" aria-label="Business card back">
  <svg class="card__shape" viewBox="0 0 653 404" preserveAspectRatio="none" aria-hidden="true">
    <polygon points="378,0 653,0 653,404 305,404 450,62" fill="var(--green)"/>
    <polyline points="375,0 447,61 302,404" fill="none" stroke="var(--yellow)" stroke-width="4"/>
  </svg>
  <div class="wordmark">Larkbend Carters</div>

  <ul class="contact">
    <li><svg class="icon"><use href="#i-phone"/></svg><span>1800 <span class="phone-l">L</span><span class="phone-b">B</span> <span class="phone-cart">Cart</span> / 1800 52 27 84</span></li>
    <li><svg class="icon"><use href="#i-mail"/></svg><span>cart@LarkbendCarters.com.au</span></li>
    <li><svg class="icon"><use href="#i-globe"/></svg><span>www.LarkbendCarters.com.au</span></li>
    <li class="contact__address"><svg class="icon"><use href="#i-pin"/></svg><span>4/17 Ormsdale Court, VIC 3264</span></li>
  </ul>

  <div class="review">
    <p class="review__title">Review our service</p>
    <p class="review__link">www.PennantOrbit.com.au</p>
  </div>
</section>

</body>
</html>
```